Camp Thornbrook 2021 Magazine Design

We are for someone to design our annual magazine/newsletter. This is a print newsletter that is a total of 20 pages. It will need to be designed in a way that is easy to share with our printers. The designer will need to be someone who is creative and easy to work with.
For those interested in this project we ask that you design 4 to 6 pages for us to view. Once we select the designer we will want the rest created in a two-week time span. For those submitting a bid please include front cover, theme & dates, mission & vision, and Make the Difference.

This link will provide the layout of the newsletter https://files.parcelvault.example/doc/7qzRk2LmVt9XwPa4NbHc6DsYe3FuJg8KoTiW5rQx/edit?share=1.

This link will provide you with the pictures that are needed and a few documents https://files.parcelvault.example/folders/4TpWx8QnRb2ZyLc7MfVd5HsJ?share=1

Details:
20 pages long (including covers)
8.5 x 11

Please message me if you need any further details.

Target Market(s)

Our alumni base. Covers all ages

Requirements
Must have
• Spelled out in document
Nice to have
• Spelled out in document
Should not have
• Spelled out in document

```html
<!DOCTYPE html>
<html lang="en">
<head>
<meta charset="utf-8">
<title>Camp Thornbrook 2021 Magazine Spreads</title>
<link rel="stylesheet" href="https://fonts.googleapis.com/css2?family=Graduate&family=Open+Sans:wght@400;600;700&display=swap">
<style>
  :root {
    --forest: #2d5a27;
    --cover-green: #2f6d22;
    --amber: #f09c12;
    --gold: #f5c21b;
    --lime-wash: #d9e39a;
    --paper: #ffffff;
    --ink: #3a3a3a;
    --rule: #2d5a27;
    --backdrop: #e6e3de;
    --cell-line: #8a8a8a;
  }
  * { box-sizing: border-box; margin: 0; padding: 0; }
  html, body { width: 935px; height: 1200px; overflow: hidden; background: var(--backdrop); }
  body { position: relative; font-family: "Open Sans", sans-serif; color: var(--ink); }

  .page { position: absolute; width: 398px; height: 515px; background: var(--paper); overflow: hidden; box-shadow: 0 2px 6px rgba(0,0,0,.18); }
  .page--cover { left: 62px; top: 64px; background: linear-gradient(180deg, var(--cover-green), #2a6420); }
  .page--contents { left: 468px; top: 64px; }
  .page--registration { left: 63px; top: 613px; height: 511px; }
  .page--sessions { left: 470px; top: 613px; height: 511px; }

  .display { font-family: "Graduate", serif; font-weight: 400; -webkit-text-stroke: 0.7px currentColor; }

  /* Cover */
  .cover-frame { position: absolute; left: 41px; top: 30px; width: 316px; height: 420px; border: 3px solid var(--gold); }
  .cover-photo { width: 100%; height: 100%; background: linear-gradient(180deg, #b9683f 0%, #6a5a34 30%, #d9963f 55%, #4a4a58 72%, #c9a74a 100%); }
  .cover-year { position: absolute; left: 0; right: 0; top: 454px; text-align: center; font-size: 28px; letter-spacing: 14px; color: var(--gold); padding-left: 14px; -webkit-text-stroke-width: 1.4px; }

  /* Contents */
  .contents-photo { position: absolute; inset: 0; background: linear-gradient(180deg, #eef0e8 0%, #d9ded0 45%, #c8cfbd 70%, #e2e6da 100%); }
  .contents-title { position: absolute; left: 0; right: 0; top: 96px; text-align: center; font-size: 15px; letter-spacing: 1.5px; color: var(--forest); padding-left: 26px; font-variant: small-caps; }
  .contents-title::after { content: ""; position: absolute; left: 208px; top: 24px; width: 4px; height: 4px; background: var(--forest); transform: rotate(45deg); }
  .contents-list { position: absolute; left: 47px; top: 134px; list-style: none; }
  .contents-row { position: relative; width: 303px; height: 17px; margin-bottom: 11.7px; color: #fff; font-size: 7.5px; }
  .contents-row svg { position: absolute; inset: 0; }
  .contents-row .entry { position: absolute; left: 20px; top: 3px; font-weight: 700; }
  .contents-row .pages { position: absolute; right: 9px; top: 3px; }
  .contents-row .box { position: absolute; left: 6px; top: 5px; width: 6px; height: 6px; border: 1px solid #fff; }
  .contents-row .box::after { content: ""; position: absolute; left: 1px; top: 1px; width: 2px; height: 2px; background: #fff; }

  /* Shared inner header */
  .page-head { position: absolute; left: 0; top: 0; width: 100%; height: 40px; background: var(--forest); border-top: 8px solid var(--amber); }
  .page-head h2 { font-variant: small-caps; font-size: 14.5px; letter-spacing: 1.4px; color: var(--amber); text-align: center; line-height: 32px; }
  .page-head .notch { position: absolute; left: 56px; bottom: -5px; width: 0; height: 0; border-left: 6px solid transparent; border-right: 6px solid transparent; border-top: 5px solid var(--forest); }
  .page-foot { position: absolute; left: 25px; right: 22px; top: 488px; border-top: 1px solid var(--rule); }
  .page-foot .folio { position: absolute; left: 0; top: 1px; width: 11px; height: 11px; background: var(--forest); color: var(--gold); font-size: 7px; font-weight: 700; text-align: center; line-height: 11px; }
  .page-foot .year { position: absolute; right: 0; top: 0; font-size: 9px; font-weight: 700; letter-spacing: 2px; color: var(--forest); }

  /* Registration */
  .reg-list { position: absolute; left: 47px; top: 61px; list-style: none; }
  .reg-list li { position: relative; width: 293px; height: 12px; margin-bottom: 4px; padding-left: 10px; font-size: 7.5px; line-height: 12px; }
  .reg-list li span { display: block; padding-left: 5px; height: 12px; }
  .reg-list li:nth-child(odd) span { background: var(--amber); }
  .reg-list li:nth-child(even) span { background: var(--lime-wash); }
  .bullet { position: absolute; left: 0; top: 3px; width: 5px; height: 5px; border: 1px solid var(--forest); }
  .bullet::after { content: ""; position: absolute; left: 1px; top: 1px; width: 1px; height: 1px; background: var(--forest); }
  .theme-frame { position: absolute; left: 47px; top: 145px; width: 292px; height: 287px; background: #dcdcdc; padding: 8px 10px; }
  .theme-art { width: 100%; height: 100%; background: linear-gradient(180deg, #c4c4c4 0%, #8e8e8e 45%, #6d6464 70%, #3a3a3a 100%); }

  /* Sessions */
  .schedule { position: absolute; left: 64px; top: 64px; border-collapse: collapse; font-size: 8.5px; }
  .schedule td { height: 15.1px; border: 1px solid var(--cell-line); padding: 0 0 0 11px; }
  .schedule td:nth-child(1) { width: 88px; }
  .schedule td:nth-child(2) { width: 115px; padding-left: 21px; }
  .schedule td:nth-child(3) { width: 64px; text-align: center; padding: 0; }
  .schedule .full td:nth-child(1) { background: var(--amber); }
  .schedule .full td:nth-child(2) { background: var(--lime-wash); }
  .ages { position: absolute; left: 63px; top: 235px; border-collapse: collapse; font-size: 8.5px; text-align: center; }
  .ages td { height: 13.5px; border: 1px solid var(--cell-line); width: 58.5px; }
  .ages td:first-child { width: 38px; text-align: left; padding-left: 5px; }
  .ages tr:first-child td:first-child { background: var(--amber); }
  .ages tr:last-child td:first-child { background: var(--lime-wash); }
  .activities { position: absolute; left: 60px; top: 290px; list-style: none; font-size: 8px; line-height: 12.5px; }
  .activities li { position: relative; padding-left: 12px; }
  .activities .bullet { top: 4px; border-color: var(--amber); }
  .activities .bullet::after { background: var(--amber); }
  .activities .more { padding-left: 0; }
  .art { position: absolute; border-radius: 4px; }
  .art--hike { left: 248px; top: 295px; width: 69px; height: 49px; background: linear-gradient(180deg, #d6eaf3, #a9cc6a); }
  .art--hoop { left: 215px; top: 348px; width: 57px; height: 54px; background: linear-gradient(180deg, #f6cfa6, #e9e9e9); }
  .art--target { left: 297px; top: 349px; width: 59px; height: 47px; background: linear-gradient(180deg, #f1e1cf, #cfe5b0); }
  .art--swim { left: 226px; top: 407px; width: 92px; height: 49px; background: linear-gradient(180deg, #eadbcb, #a9daf2); }
</style>
</head>
<body>

<section class="page page--cover" aria-label="Front cover">
  <div class="cover-frame">
    <div class="cover-photo" role="img" aria-label="Photograph of eight colourful signed camp-year boards mounted on a wall"></div>
  </div>
  <div class="cover-year display">2021</div>
</section>

<section class="page page--contents" aria-label="Table of contents">
  <div class="contents-photo" role="img" aria-label="Faded photograph of a wooden post and tree trunk in a wooded clearing"></div>
  <h1 class="contents-title display">Table of Contents</h1>
  <ol class="contents-list">
    <li class="contents-row"><svg width="303" height="17"><polygon points="0,0 182,0 188,8.5 182,17 0,17" fill="#f09c12"/><polygon points="187,0 303,0 303,17 187,17 193,8.5" fill="#f09c12"/></svg><i class="box"></i><span class="entry">Make the Difference</span><span class="pages">Page 3</span></li>
    <li class="contents-row"><svg width="303" height="17"><polygon points="0,0 182,0 188,8.5 182,17 0,17" fill="#2d5a27"/><polygon points="187,0 303,0 303,17 187,17 193,8.5" fill="#2d5a27"/></svg><i class="box"></i><span class="entry">Golf Tournament</span><span class="pages">Pages 4 &amp; 5</span></li>
    <li class="contents-row"><svg width="303" height="17"><polygon points="0,0 182,0 188,8.5 182,17 0,17" fill="#f09c12"/><polygon points="187,0 303,0 303,17 187,17 193,8.5" fill="#f09c12"/></svg><i class="box"></i><span class="entry">2021 Theme and Dates</span><span class="pages">Pages 6 &amp; 7</span></li>
    <li class="contents-row"><svg width="303" height="17"><polygon points="0,0 182,0 188,8.5 182,17 0,17" fill="#2d5a27"/><polygon points="187,0 303,0 303,17 187,17 193,8.5" fill="#2d5a27"/></svg><i class="box"></i><span class="entry">Where Are They Now: Dale Whitmore</span><span class="pages">Pages 8 &amp; 9</span></li>
    <li class="contents-row"><svg width="303" height="17"><polygon points="0,0 182,0 188,8.5 182,17 0,17" fill="#f09c12"/><polygon points="187,0 303,0 303,17 187,17 193,8.5" fill="#f09c12"/></svg><i class="box"></i><span class="entry">2019 Donors</span><span class="pages">Pages 10, 11, &amp; 12</span></li>
    <li class="contents-row"><svg width="303" height="17"><polygon points="0,0 182,0 188,8.5 182,17 0,17" fill="#2d5a27"/><polygon points="187,0 303,0 303,17 187,17 193,8.5" fill="#2d5a27"/></svg><i class="box"></i><span class="entry">2019 Thornbrook Awards</span><span class="pages">Page 13</span></li>
    <li class="contents-row"><svg width="303" height="17"><polygon points="0,0 182,0 188,8.5 182,17 0,17" fill="#f09c12"/><polygon points="187,0 303,0 303,17 187,17 193,8.5" fill="#f09c12"/></svg><i class="box"></i><span class="entry">Hawk Ridge</span><span class="pages">Pages 14 &amp;15</span></li>
    <li class="contents-row"><svg width="303" height="17"><polygon points="0,0 182,0 188,8.5 182,17 0,17" fill="#2d5a27"/><polygon points="187,0 303,0 303,17 187,17 193,8.5" fill="#2d5a27"/></svg><i class="box"></i><span class="entry">Mission/Vision</span><span class="pages">Pages 16 &amp; 17</span></li>
    <li class="contents-row"><svg width="303" height="17"><polygon points="0,0 182,0 188,8.5 182,17 0,17" fill="#f09c12"/><polygon points="187,0 303,0 303,17 187,17 193,8.5" fill="#f09c12"/></svg><i class="box"></i><span class="entry">A Place We Call Home</span><span class="pages">Page 18</span></li>
    <li class="contents-row"><svg width="303" height="17"><polygon points="0,0 182,0 188,8.5 182,17 0,17" fill="#2d5a27"/><polygon points="187,0 303,0 303,17 187,17 193,8.5" fill="#2d5a27"/></svg><i class="box"></i><span class="entry">Memorials</span><span class="pages">Page 19</span></li>
  </ol>
</section>

<section class="page page--registration" aria-label="Registration and other information">
  <header class="page-head"><h2 class="display">Registration and Other Information</h2><i class="notch"></i></header>
  <ul class="reg-list">
    <li><i class="bullet"></i><span>Registration begins on January 1, 2021</span></li>
    <li><i class="bullet"></i><span>Register online at campthornbrook.org</span></li>
    <li><i class="bullet"></i><span>Super Early Bird Discount ($20) if registered before April 1st</span></li>
    <li><i class="bullet"></i><span>Early Bird Discount ($10) if registered in the month of April</span></li>
  </ul>
  <div class="theme-frame">
    <div class="theme-art" role="img" aria-label="2021 theme poster “Resurrection” with a crescent sunrise over rocky mountains and a verse from John 11:25"></div>
  </div>
  <footer class="page-foot"><span class="folio">6</span><span class="year">2021</span></footer>
</section>

<section class="page page--sessions" aria-label="Sessions and dates">
  <header class="page-head"><h2 class="display">Session and Dates</h2><i class="notch" style="left:111px"></i></header>
  <table class="schedule">
    <tr class="full"><td>Session 1</td><td>May&nbsp; 30 - June&nbsp;&nbsp; 5</td><td>($285)</td></tr>
    <tr><td>Short Session 1</td><td>May&nbsp; 30 - June&nbsp;&nbsp; 2</td><td>($175)</td></tr>
    <tr class="full"><td>Session 2</td><td>June&nbsp;&nbsp;&nbsp; 6 - June 17</td><td>($425)</td></tr>
    <tr><td>Session 2B</td><td>June&nbsp;&nbsp;&nbsp; 6 - June 12</td><td>($285)</td></tr>
    <tr class="full"><td>Session 3</td><td>June 27 - July&nbsp;&nbsp;&nbsp; 8</td><td>($425)</td></tr>
    <tr><td>Session 3B</td><td>June 27 - July&nbsp;&nbsp;&nbsp; 3</td><td>($285)</td></tr>
    <tr class="full"><td>Session 4</td><td>July&nbsp; 11 - July&nbsp; 22</td><td>($425)</td></tr>
    <tr><td>Session 4B</td><td>July&nbsp; 11 - July&nbsp; 17</td><td>($285)</td></tr>
    <tr class="full"><td>Session 5</td><td>July&nbsp; 25 - July&nbsp; 31</td><td>($285)</td></tr>
    <tr><td>Short Session 2</td><td>July&nbsp; 25 - July&nbsp; 28</td><td>($175)</td></tr>
  </table>
  <table class="ages">
    <tr><td>Group</td><td>1</td><td>2</td><td>3</td><td>4</td></tr>
    <tr><td>Age</td><td>8-10 Years</td><td>11-12 Years</td><td>13-14 Years</td><td>15-18 Years</td></tr>
  </table>
  <ul class="activities">
    <li><i class="bullet"></i>Archery Tag</li>
    <li><i class="bullet"></i>Blob</li>
    <li><i class="bullet"></i>Horseback Riding</li>
    <li><i class="bullet"></i>Hiking</li>
    <li><i class="bullet"></i>Gaga Ball</li>
    <li><i class="bullet"></i>Golden Goal (New)</li>
    <li><i class="bullet"></i>Rappelling</li>
    <li><i class="bullet"></i>Archery</li>
    <li><i class="bullet"></i>Hatchet Throwing (New)</li>
    <li><i class="bullet"></i>Basketball</li>
    <li><i class="bullet"></i>Arts and Crafts</li>
    <li><i class="bullet"></i>9 Square in the Air</li>
    <li><i class="bullet"></i>Swimming</li>
    <li class="more">And much more!</li>
  </ul>
  <div class="art art--hike" role="img" aria-label="Illustration of hikers climbing a sunny green hill"></div>
  <div class="art art--hoop" role="img" aria-label="Illustration of a basketball dropping into a hoop"></div>
  <div class="art art--target" role="img" aria-label="Illustration of an arrow in an archery target"></div>
  <div class="art art--swim" role="img" aria-label="Illustration of a child swimming"></div>
  <footer class="page-foot"><span class="folio">7</span><span class="year">2021</span></footer>
</section>

</body>
</html>
```